Brindle Recycling needs a new web design

We need a new web design for our company based in Austin, TX. We resell and recycling electronics such as laptops, computer components, Zelvotabs, Quorns, etc. Since our inception over ten years ago, we’ve become one of the premier electronics recycling and remarketing companies in Austin, Texas.

```html
<!DOCTYPE html>
<html lang="en">
<head>
<meta charset="utf-8">
<title>Brindle Recycling — Services</title>
<link rel="stylesheet" href="https://fonts.googleapis.com/css2?family=Raleway:wght@400;500;700&family=Roboto:wght@300;400;500;700&display=swap">
<style>
  :root {
    --page-bg: #f6f6f6;
    --about-bg: #ececec;
    --ink: #1d1d1f;
    --muted: #666666;
    --body-text: #6f6f6f;
    --brand-blue: #1a6fc2;
    --band-blue: #1b6fbf;
    --band-blue-dark: #1462b0;
    --white: #ffffff;
  }
  * { box-sizing: border-box; margin: 0; padding: 0; }
  html, body { width: 1200px; height: 1000px; overflow: hidden; }
  body { position: relative; background: var(--page-bg); font-family: "Roboto", Arial, sans-serif; color: var(--ink); }

  .services { position: absolute; left: 0; top: 0; width: 1200px; height: 553px; background: var(--page-bg); }
  .service { position: absolute; top: 53px; text-align: center; }
  .service--ewaste { left: 190px; width: 399px; }
  .service--pickup { left: 614px; width: 396px; }
  .service__photo { display: block; width: 100%; height: 181px; }
  .service--ewaste .service__photo { background: linear-gradient(135deg, #1b2a3c 0%, #2a4a5a 40%, #3b7a4a 70%, #1c2b44 100%); }
  .service--pickup .service__photo { background: linear-gradient(100deg, #2e2a26 0%, #6b5e4c 40%, #d9c29a 55%, #5a5046 75%, #3a3530 100%); }
  .service__title { margin-top: 32px; font-family: "Raleway", Arial, sans-serif; font-weight: 700; font-size: 24px; line-height: 28px; color: var(--ink); }
  .service__tagline { margin-top: 10px; font-size: 15px; line-height: 20px; color: var(--muted); }
  .service__text { margin: 20px auto 0; width: 370px; font-weight: 300; font-size: 13.5px; line-height: 19px; color: var(--body-text); }
  .btn { display: inline-flex; align-items: center; justify-content: center; height: 40px; font-family: "Roboto", Arial, sans-serif; font-weight: 500; font-size: 11px; letter-spacing: 0.2px; text-transform: uppercase; text-decoration: none; }
  .btn--outline-blue { width: 148px; border: 2px solid var(--brand-blue); color: var(--ink); background: transparent; }
  .service .btn { position: absolute; top: 409px; left: 50%; transform: translateX(-50%); }

  .cta-band { position: absolute; left: 0; top: 553px; width: 1200px; height: 290px; text-align: center; color: var(--white);
    background: linear-gradient(180deg, var(--band-blue) 0%, #1a6cbc 60%, #1d72c2 100%); }
  .cta-band__title { position: absolute; top: 54px; width: 100%; font-family: "Raleway", Arial, sans-serif; font-weight: 700; font-size: 26px; line-height: 30px; }
  .cta-band__text { position: absolute; top: 90px; width: 100%; font-family: "Raleway", Arial, sans-serif; font-size: 18px; line-height: 36px; }
  .cta-band .btn { position: absolute; top: 194px; }
  .btn--solid { left: 441px; width: 148px; height: 39px; background: var(--band-blue-dark); color: var(--white); }
  .btn--outline-white { left: 614px; width: 109px; border: 2px solid var(--white); color: var(--white); }

  .about { position: absolute; left: 0; top: 843px; width: 1200px; height: 157px; background: var(--about-bg); }
  .about__photo { position: absolute; left: 0; top: 0; width: 500px; height: 157px; background: linear-gradient(120deg, #f2f2f0 0%, #e4e4e2 45%, #d8dadc 70%, #eeeeec 100%); }
  .about__title { position: absolute; left: 568px; top: 64px; font-family: "Raleway", Arial, sans-serif; font-weight: 700; font-size: 24px; line-height: 28px; color: var(--ink); }
  .about__text { position: absolute; left: 566px; top: 113px; width: 450px; font-weight: 300; font-size: 14px; line-height: 19px; color: var(--body-text); }
</style>
</head>
<body>
  <section class="services">
    <article class="service service--ewaste">
      <div class="service__photo" role="img" aria-label="Circuit boards, hard drives and computer parts laid out on a dark surface"></div>
      <h2 class="service__title">Electronic Recycling</h2>
      <p class="service__tagline">Environmentally Friendly</p>
      <p class="service__text">At Brindle Recycling, we strive to keep the environment clean through our wide range of services. Our E-Waste Recycling services were designed to simplify the recycling process for residents in the Austin area. Contact us today and see how you can contribute to making this world a cleaner place.</p>
      <a class="btn btn--outline-blue" href="#">Schedule a pickup</a>
    </article>
    <article class="service service--pickup">
      <div class="service__photo" role="img" aria-label="Worker loading a recycling bin into a pickup truck at sunset"></div>
      <h2 class="service__title">Recycling Pickup</h2>
      <p class="service__tagline">We Come To You</p>
      <p class="service__text">At Brindle Recycling, we go out of our way to make sure your recycling process is made easy as possible. Our Recycling Pickup service is designed to simplify all of your recycling needs . Take a look at all the services we offer and get in touch to see how you can start the process today!</p>
      <a class="btn btn--outline-blue" href="#">Schedule a pickup</a>
    </article>
  </section>

  <section class="cta-band">
    <h2 class="cta-band__title">MAKE A DIFFERENCE</h2>
    <p class="cta-band__text">Have a passion to keep our world clean and are here to guide you<br>through all the stages of the recycling process.</p>
    <a class="btn btn--solid" href="#">Schedule a pickup</a>
    <a class="btn btn--outline-white" href="#">Contact us</a>
  </section>

  <section class="about">
    <div class="about__photo" role="img" aria-label="Office desk with a tablet, desk phone, smartphone, charts and an apple"></div>
    <h2 class="about__title">About Dale Whitmore - CEO</h2>
    <p class="about__text">As the CEO of Brindle Recycling, Dale Whitmore is responsible for running all facets of the business. Dale has a proven executive management track record and over 20 years of experience driving growth in the Recycling industry.</p>
  </section>
</body>
</html>
```